Seeking a new website design for electrical contracting company

Brisket & Vane electrical contracting needs a new website for brisket-vane.example

We are looking for modern and something real cool with motion for a landing page. we have some cool images from our photo shoot. maybe even 3d motion our existing logo. we would like something we can edit with news and events and update a past project page. Also allow to take payment
stock images at
https://lorapellwinphotos.picvault-demo.example/Brisket-and-Vane

Target Market(s)

construction , home owners , business owners,

Industry/Entity Type

construction , electrical

Coding

Number of Pages Required

5+ page

Font styles to use
Serif
Sans Serif

Colors
0054AA
0677BA
7BADD7
CADEEF
E8F1F8
0094D4
00A9DD
6FCCEA
C7EBF8
E9F6FB
FFF300
FFF600
FEFA6F
FFFEC7
FFFEE8

Requirements
Must have
• excitement, motion, selling professionalism,

```html
<!DOCTYPE html>
<html lang="en">
<head>
<meta charset="utf-8">
<title>Brisket &amp; Vane Electrical Contractors</title>
<link rel="stylesheet" href="https://fonts.googleapis.com/css2?family=League+Spartan:wght@600;700&family=Lato:wght@400;700&display=swap">
<style>
:root{
  --blue:#0054AA;
  --blue-mid:#0677BA;
  --blue-deep:#00397a;
  --blue-night:#022a5c;
  --sky:#0094D4;
  --sky-pale:#E8F1F8;
  --sky-soft:#CADEEF;
  --yellow:#FFF300;
  --yellow-soft:#FEFA6F;
  --yellow-pale:#FFFEE8;
  --white:#ffffff;
  --text:#2e3a4d;
}
*{box-sizing:border-box;margin:0;padding:0}
html,body{width:1200px;height:4542px;overflow:hidden}
body{font-family:"Lato",sans-serif;color:var(--text);background:var(--white);position:relative}
section,header,footer{position:absolute;left:0;width:1200px}
.display{font-family:"League Spartan",sans-serif;font-weight:700;text-transform:uppercase;letter-spacing:.2px}
.eyebrow{font-size:22px;color:var(--sky)}
.on-dark .eyebrow{color:var(--yellow)}
.btn{position:absolute;display:flex;align-items:center;justify-content:center;background:var(--yellow);color:var(--blue);font-weight:700;font-size:15px;border-radius:2px}
.btn.blue{background:var(--blue);color:var(--white)}
.photo{position:absolute;border-radius:4px}

/* hero */
.hero{top:0;height:645px;background:linear-gradient(100deg,var(--blue-night) 0%,#04336d 55%,#0a3a78 100%);overflow:hidden}
.hero-photo{position:absolute;left:600px;top:0;width:600px;height:645px;background:linear-gradient(160deg,#5f6a78 0%,#8e949b 45%,#6d7480 70%,#3c4552 100%);clip-path:polygon(150px 0,600px 0,600px 645px,0 645px)}
.brand{position:absolute;left:111px;top:32px;display:flex;align-items:center;gap:12px;color:var(--white)}
.brand-mark{width:70px;height:70px;border:4px solid var(--white);border-radius:50%}
.brand-name{font-family:"League Spartan",sans-serif;font-weight:700;font-size:31px;line-height:1;text-transform:uppercase}
.nav{position:absolute;top:40px;left:515px;display:flex;gap:36px;align-items:center;font-size:14px;color:var(--white)}
.nav .active{background:var(--yellow);color:var(--blue);padding:6px 9px;border-radius:2px;font-weight:700}
.hero h1{position:absolute;left:111px;top:180px;font-size:53px;line-height:70px;color:var(--white)}
.hero h1 em{font-style:normal;color:var(--yellow)}
.hero p{position:absolute;left:111px;top:400px;width:440px;font-size:19px;line-height:32px;color:var(--white)}

/* services */
.services{top:645px;height:578px;background:var(--blue)}
.services .eyebrow{position:absolute;left:111px;top:82px}
.services h2{position:absolute;left:111px;top:132px;font-size:31px;line-height:40px;color:var(--white)}
.services .lead{position:absolute;left:680px;top:76px;width:420px;font-size:18px;line-height:30px;color:var(--white)}
.svc{position:absolute;top:259px;width:224px;height:233px;background:var(--yellow);color:var(--blue);text-align:center}
.svc svg{margin-top:34px}
.svc h3{font-size:17px;line-height:28px;font-weight:700;margin-top:18px;padding:0 14px}
.svc .more{display:block;margin-top:14px;font-weight:700;font-size:16px}
.svc.light{background:var(--white)}
.svc.light .more{color:var(--sky)}

/* about */
.about{top:1223px;height:570px}
.about .eyebrow{position:absolute;left:645px;top:85px}
.about h2{position:absolute;left:645px;top:132px;font-size:32px;line-height:40px;color:var(--blue)}
.about p{position:absolute;left:645px;width:430px;font-size:14.5px;line-height:24px}

/* projects */
.projects{top:1793px;height:750px;text-align:center}
.projects .eyebrow{position:absolute;left:0;width:1200px;top:36px}
.projects h2{position:absolute;left:0;width:1200px;top:78px;font-size:32px;color:var(--blue)}
.projects .lead{position:absolute;left:300px;width:600px;top:126px;font-size:15px;line-height:24px}
.proj{position:absolute;top:224px;width:308px}
.proj .photo{position:static;height:253px;border-radius:2px}
.proj h3{font-family:"League Spartan",sans-serif;font-weight:600;font-size:22px;color:var(--blue);margin-top:20px}
.proj p{font-size:14.5px;line-height:24px;margin:12px 14px 0}
.proj .btn{position:relative;margin:20px auto 0;width:128px;height:36px}

/* cta */
.cta{top:2543px;height:371px;background:linear-gradient(90deg,#fff200,var(--yellow-soft) 50%,#fff200);text-align:center;color:var(--blue)}
.cta .kicker{position:absolute;left:0;width:1200px;top:70px;font-size:21px;color:var(--blue-mid)}
.cta h2{position:absolute;left:0;width:1200px;top:110px;font-size:32px}
.cta p{position:absolute;left:275px;width:650px;top:163px;font-size:14.5px;line-height:24px;color:var(--text)}

/* news */
.news{top:2914px;height:624px}
.news .eyebrow{position:absolute;left:111px;top:106px}
.news h2{position:absolute;left:111px;top:152px;font-size:32px;line-height:40px;color:var(--blue)}
.news h3{position:absolute;left:111px;top:254px;width:340px;font-size:17px;line-height:22px;font-weight:700;color:var(--blue)}
.news p{position:absolute;left:111px;top:320px;width:400px;font-size:14.5px;line-height:22.5px}

/* testimonials */
.testi{top:3538px;height:574px;background:var(--blue);color:var(--white);text-align:center}
.testi .kicker{position:absolute;left:0;width:1200px;top:68px;font-size:22px}
.testi h2{position:absolute;left:0;width:1200px;top:113px;font-size:32px}
.testi .lead{position:absolute;left:370px;width:460px;top:156px;font-size:15px;line-height:24px}
.card{position:absolute;top:234px;width:317px;height:228px;background:var(--yellow);color:var(--text);text-align:left;padding:26px 24px}
.card.light{background:var(--white)}
.stars{color:var(--blue);font-size:17px;letter-spacing:2px}
.card.light .stars{color:var(--sky)}
.card q{display:block;margin-top:18px;font-size:14.5px;line-height:22px;quotes:none}
.card .who{margin-top:22px;font-weight:700;font-size:17px;color:var(--blue)}
.card .date{font-size:12px;margin-top:6px}
.pager{position:absolute;top:488px;left:568px;display:flex;gap:6px}
.pager span{width:18px;height:6px;border-radius:3px;background:var(--white)}
.pager span:first-child{background:var(--yellow)}

/* footer */
.footer{top:4112px;height:430px;background:var(--blue-night);color:var(--white)}
.footer h4{position:absolute;top:72px;font-size:20px;font-weight:700}
.footer .col{position:absolute;top:120px;font-size:14.5px;line-height:26px}
.footer ul{list-style:none}
.footer li{line-height:38.5px}
.contact-row{display:flex;gap:20px;align-items:flex-start;margin-bottom:30px}
.social{display:flex;gap:15px;margin-top:32px}
.social span{width:36px;height:36px;border-radius:4px;background:var(--sky-soft)}
.social span:first-child{background:var(--yellow)}
.copyright{position:absolute;left:0;width:1200px;top:392px;text-align:center;font-size:12px;border-top:1px solid rgba(255,255,255,.12);padding-top:14px}
</style>
</head>
<body>

<header class="hero">
  <div class="hero-photo" role="img" aria-label="Photo of the electrical crew standing in front of company service vans"></div>
  <div class="brand">
    <div class="brand-mark"></div>
    <div class="brand-name">Brisket &amp; Vane</div>
  </div>
  <nav class="nav">
    <span class="active">Home</span><span>About Us</span><span>Services</span><span>Projects</span><span>News &amp; Events</span><span>Contact</span>
  </nav>
  <h1 class="display">Bringing <em>Power</em><br><em>and Precision</em><br>to Every Project</h1>
  <p>High-performance electrical contracting for commercial, industrial, and mission-critical projects.</p>
  <a class="btn" style="left:111px;top:523px;width:164px;height:38px">Request a Quote</a>
</header>

<section class="services on-dark">
  <div class="eyebrow">Our Services</div>
  <h2 class="display">Scalable Power Solutions<br>Seamless Execution</h2>
  <p class="lead">From design to installation, we deliver reliable, code-compliant electrical systems built for performance. We handle complex electrical builds with expert planning, reliable installation, and long-term support.</p>

  <div class="svc" style="left:111px">
    <svg width="66" height="66" viewBox="0 0 66 66" fill="none" stroke="#0054AA" stroke-width="2"><circle cx="33" cy="33" r="30"/><path d="M26 14v12M40 14v12M21 26h24v8a12 12 0 0 1-24 0z M33 46v10"/></svg>
    <h3>Commercial Electrical Contracting</h3><span class="more">Read More</span>
  </div>
  <div class="svc light" style="left:363px">
    <svg width="66" height="66" viewBox="0 0 66 66" fill="none" stroke="#0094D4" stroke-width="2"><circle cx="33" cy="33" r="30"/><path d="M33 14a12 12 0 0 0-7 22v6h14v-6a12 12 0 0 0-7-22z M27 47h12M29 52h8 M35 20l-5 9h6l-5 8"/></svg>
    <h3>Industrial Electrical Solutions</h3><span class="more">Read More</span>
  </div>
  <div class="svc" style="left:613px">
    <svg width="66" height="66" viewBox="0 0 66 66" fill="none" stroke="#0054AA" stroke-width="2"><path d="M37 10L24 36h10l-5 20 14-28H33z M12 33h6M48 33h6M17 17l4 4M49 17l-4 4M17 49l4-4M49 49l-4-4"/></svg>
    <h3>Emergency Power &amp; Generators</h3><span class="more">Read More</span>
  </div>
  <div class="svc" style="left:865px">
    <svg width="66" height="66" viewBox="0 0 66 66" fill="none" stroke="#0054AA" stroke-width="2"><rect x="12" y="10" width="42" height="34"/><rect x="18" y="16" width="30" height="22"/><path d="M35 19l-6 9h6l-4 8 M16 44v10h34V44 M22 50h22"/></svg>
    <h3>Power Distribution &amp; Panel Upgrades</h3><span class="more">Read More</span>
  </div>
</section>

<section class="about">
  <div class="photo" style="left:111px;top:86px;width:453px;height:435px;background:linear-gradient(150deg,#7a6a60 0%,#c9c9c6 40%,#e6e6e4 60%,#6d6f74 100%)" role="img" aria-label="Photo of a technician standing beside a white company van"></div>
  <div class="eyebrow">About Us</div>
  <h2 class="display">Powering Projects<br>Building Trust</h2>
  <p style="top:234px">Brisket &amp; Vane is a full-service electrical contracting company delivering high-performance solutions across commercial, industrial, and mission-critical sectors.</p>
  <p style="top:332px">From initial planning through final inspection, we bring technical precision, skilled craftsmanship, and decades of field-tested experience to every project. Whether you're building new, upgrading infrastructure, or maintaining complex systems — we wire with purpose, integrity, and pride.</p>
  <a class="btn" style="left:645px;top:484px;width:128px;height:36px">Read More</a>
</section>

<section class="projects">
  <div class="eyebrow">Past Projects</div>
  <h2 class="display">Projects That Speak for Themselves</h2>
  <p class="lead">Built for performance. Trusted for precision. We bring deep expertise, clean execution, and serious attention to detail — powering commercial and industrial projects that can't afford to fail.</p>
  <div class="proj" style="left:111px">
    <div class="photo" style="background:linear-gradient(180deg,#a9b8c8,#6c7a88)" role="img" aria-label="Photo of a worker among high-voltage substation equipment"></div>
    <h3>Commercial Projects</h3>
    <p>Lorem ipsum dolor sit amet, consectetur adipiscing elit, sed do eiusmod tempor incididunt ut labore et magna aliqua</p>
    <a class="btn">View All</a>
  </div>
  <div class="proj" style="left:446px">
    <div class="photo" style="background:linear-gradient(160deg,#8a95a3,#b4683e 60%,#3f4a57)" role="img" aria-label="Photo of two engineers in hard hats reviewing a laptop at an industrial plant"></div>
    <h3>Industrial Projects</h3>
    <p>Lorem ipsum dolor sit amet, consectetur adipiscing elit, sed do eiusmod tempor incididunt ut labore et magna aliqua</p>
    <a class="btn">View All</a>
  </div>
  <div class="proj" style="left:781px">
    <div class="photo" style="background:linear-gradient(160deg,#e3e5e8,#c9d24a 55%,#9aa0a8)" role="img" aria-label="Photo of two electricians in hi-vis vests installing ceiling wiring"></div>
    <h3>Specialized Projects</h3>
    <p>Lorem ipsum dolor sit amet, consectetur adipiscing elit, sed do eiusmod tempor incididunt ut labore et magna aliqua</p>
    <a class="btn">View All</a>
  </div>
</section>

<section class="cta">
  <div class="kicker">Ready to Power Up?</div>
  <h2 class="display">Powering Your Future, Today</h2>
  <p>Expert electrical solutions for every project. Reliable, efficient, and built to last. Whether you're planning a new build, upgrading systems, or need emergency electrical services, we're here to bring your project to life. Let's get started today!</p>
  <a class="btn blue" style="left:513px;top:260px;width:174px;height:36px">Start Your Project</a>
</section>

<section class="news">
  <div class="photo" style="left:634px;top:87px;width:453px;height:451px;background:linear-gradient(160deg,#6f88a6 0%,#3e4754 45%,#d8d6cf 70%,#4a4f58 100%)" role="img" aria-label="Photo of the crew reviewing blueprints on a van hood"></div>
  <div class="eyebrow">News &amp; Events</div>
  <h2 class="display">Stay Updated with Our<br>Latest News &amp; Events</h2>
  <h3>Event 1: Powering the Future — Industry Conference 2025</h3>
  <p>Whether it's a new project, an upcoming industry event, or important company news, you can find all the latest happenings here. Join us at this year's premier electrical industry event where we'll be showcasing our innovative solutions and sharing insights on the future of electrical contracting.</p>
  <a class="btn" style="left:111px;top:481px;width:128px;height:36px">View All</a>
</section>

<section class="testi">
  <div class="kicker">Our Testimonials</div>
  <h2 class="display">What Our Clients Are Saying</h2>
  <p class="lead">We take pride in building lasting relationships and delivering exceptional electrical services.</p>
  <div class="card" style="left:111px">
    <div class="stars">★★★★★</div>
    <q>Excepteur sint occaecat cupidatat non proident, sunt in culpa qui officia deserunt mollit anim id est laborum.</q>
    <div class="who">Halvorsen</div><div class="date">Apr 18 2025</div>
  </div>
  <div class="card light" style="left:441px">
    <div class="stars">★★★★★</div>
    <q>Excepteur sint occaecat cupidatat non proident, sunt in culpa qui officia deserunt mollit anim id est laborum.</q>
    <div class="who">Priya</div><div class="date">Apr 18 2025</div>
  </div>
  <div class="card" style="left:772px">
    <div class="stars">★★★★★</div>
    <q>Excepteur sint occaecat cupidatat non proident, sunt in culpa qui officia deserunt mollit anim id est laborum.</q>
    <div class="who">Odette</div><div class="date">Apr 18 2025</div>
  </div>
  <div class="pager"><span></span><span></span><span></span></div>
</section>

<footer class="footer">
  <h4 style="left:115px">About Us</h4>
  <div class="col" style="left:113px;width:280px">
    <p>Whether you're building new, upgrading infrastructure, or maintaining complex systems — we wire with purpose, integrity, and pride.</p>
    <div class="social" aria-label="Social links"><span></span><span></span><span></span><span></span></div>
  </div>

  <h4 style="left:463px">Contact Us</h4>
  <div class="col" style="left:463px;top:128px;width:260px">
    <div class="contact-row"><svg width="18" height="22" viewBox="0 0 18 22" fill="none" stroke="#fff" stroke-width="1.6"><path d="M9 21s7-7 7-12A7 7 0 0 0 2 9c0 5 7 12 7 12z"/><circle cx="9" cy="9" r="2.5"/></svg><span>418 Larkfield Rd.<br>Easton Falls NH 03990</span></div>
    <div class="contact-row"><svg width="18" height="18" viewBox="0 0 18 18" fill="none" stroke="#fff" stroke-width="1.6"><path d="M3 1h4l1.5 4-2.5 1.5a10 10 0 0 0 5.5 5.5L13 9.5l4 1.5v4a2 2 0 0 1-2 2A15 15 0 0 1 1 3a2 2 0 0 1 2-2z"/></svg><span>1-555-014-2297</span></div>
    <div class="contact-row"><svg width="18" height="14" viewBox="0 0 18 14" fill="none" stroke="#fff" stroke-width="1.6"><rect x="1" y="1" width="16" height="12"/><path d="M1 1l8 7 8-7"/></svg><span>office@brisket-vane.example</span></div>
  </div>

  <h4 style="left:761px">Quick Links</h4>
  <ul class="col" style="left:761px;top:112px"><li>Home</li><li>About Us</li><li>Services</li><li>Projects</li><li>News &amp; Events</li></ul>

  <h4 style="left:976px">Other Links</h4>
  <ul class="col" style="left:976px;top:112px"><li>FAQs</li><li>Support</li><li>Contact Us</li><li>Privacy Policy</li><li>Terms of Service</li></ul>

  <div class="copyright">Copyright © 2025 Brisket &amp; Vane electrical contracting. All rights reserved.</div>
</footer>

</body>
</html>
```